Business Card Design Project

Keep it simple , using logo and colors that compliment. Logo on one side with complimentary back ground color. Other side, personal info with possible complimentary design/colors

Target Market(s)

we are a non for profit that will be seeking donations . Both monetary and in kind

Industry/Entity Type

Business

Font styles to use
Sans Serif

Colors

Designer to choose colors to be used in the design.

```html
<!DOCTYPE html>
<html lang="en">
<head>
<meta charset="utf-8">
<title>Grand Stride – Business Card</title>
<link href="https://fonts.googleapis.com/css2?family=Open+Sans:wght@300;400;700&display=swap" rel="stylesheet">
<style>
  :root {
    --navy: #262c4f;
    --yellow: #e8cc00;
    --paper: #ffffff;
    --paper-back: #f0f0ee;
    --backdrop: #e9e9e9;
    --ghost: #e3e3e0;
    --ink: #262c4f;
    --muted: #3a3f5c;
  }
  * { margin: 0; padding: 0; box-sizing: border-box; }
  html, body { width: 1200px; height: 675px; overflow: hidden; }
  body {
    background: var(--backdrop);
    font-family: "Open Sans", Arial, sans-serif;
    color: var(--ink);
    position: relative;
  }
  .card {
    position: absolute;
    top: 183px;
    width: 540px;
    height: 309px;
    overflow: hidden;
    box-shadow: 0 6px 18px rgba(0,0,0,0.12);
  }
  .card--front {
    left: 40px;
    background: var(--paper);
    display: flex; align-items: center; justify-content: center; gap: 14px;
  }
  .card--back { left: 620px; background: var(--paper-back); }

  .brand-mark {
    width: 18px; height: 18px;
    background: var(--navy);
    flex: none;
  }
  .brand-name {
    font-weight: 300;
    font-size: 34px;
    color: var(--navy);
    white-space: nowrap;
    line-height: 1;
  }

  .back-brand {
    position: absolute; left: 34px; top: 78px;
    display: flex; align-items: center; gap: 10px;
  }
  .back-brand .brand-mark { width: 12px; height: 12px; }
  .back-brand .brand-name { font-size: 22px; }

  .ghost-name {
    position: absolute; left: 14px; top: 196px;
    font-weight: 300; font-size: 54px;
    color: var(--ghost);
    white-space: nowrap;
    line-height: 1;
  }

  .rule {
    position: absolute; left: 270px; right: 0; top: 80px;
    height: 1px; background: var(--yellow);
  }
  .person { position: absolute; left: 290px; top: 92px; }
  .person__name { font-weight: 700; font-size: 15px; color: var(--navy); line-height: 20px; }
  .person__role { font-size: 9px; color: var(--muted); line-height: 12px; }
  .person__divider {
    width: 230px; margin: 8px 0 6px -6px;
    border-top: 1px dotted var(--yellow);
  }
  .contact { list-style: none; font-size: 11px; color: var(--navy); }
  .contact li { display: flex; align-items: center; gap: 8px; line-height: 17px; white-space: nowrap; }
  .contact svg { width: 10px; height: 10px; fill: var(--navy); flex: none; }
  .contact .pair { display: flex; gap: 6px; align-items: center; }

  .bands { position: absolute; left: 0; top: 0; width: 540px; height: 309px; }
</style>
</head>
<body>

<section class="card card--front" aria-label="Card front">
  <span class="brand-mark"></span>
  <span class="brand-name">Grand Stride</span>
</section>

<section class="card card--back" aria-label="Card back">
  <div class="ghost-name" aria-hidden="true">Grand Stride</div>

  <svg class="bands" viewBox="0 0 540 309" aria-hidden="true">
    <polygon points="330,258 352,244 540,244 540,258" fill="var(--yellow)"/>
    <polygon points="150,309 330,258 540,258 540,309" fill="var(--navy)"/>
  </svg>

  <div class="back-brand">
    <span class="brand-mark"></span>
    <span class="brand-name">Grand Stride</span>
  </div>

  <div class="rule"></div>

  <div class="person">
    <div class="person__name">Your Long Name</div>
    <div class="person__role">Owner / President</div>
    <div class="person__divider"></div>
    <ul class="contact">
      <li>
        <svg viewBox="0 0 10 10"><path d="M5 0a3.5 3.5 0 0 0-3.5 3.5C1.5 6 5 10 5 10s3.5-4 3.5-6.5A3.5 3.5 0 0 0 5 0zm0 5a1.5 1.5 0 1 1 0-3 1.5 1.5 0 0 1 0 3z"/></svg>
        Your Commercial or office address
      </li>
      <li>
        <svg viewBox="0 0 10 10"><path d="M2 0h2l1 2.5-1.3 1a6 6 0 0 0 2.8 2.8l1-1.3L10 6v2c0 1-1 2-2 2A8 8 0 0 1 0 2c0-1 1-2 2-2z"/></svg>
        <span class="pair">00.00.00.0000
          <svg viewBox="0 0 10 10"><path d="M2 0h5v3H2zM0 3.5h10V10H0zm2 2v1h1v-1zm2.5 0v1h1v-1zm2.5 0v1h1v-1zM2 8v1h1V8zm2.5 0v1h1V8zM7 8v1h1V8z"/></svg>
          00.00.00.0000</span>
      </li>
      <li>
        <svg viewBox="0 0 10 10"><path d="M0 1.5h10v7H0zm1 1v.3L5 5.5l4-2.7v-.3z"/></svg>
        yourname@yourwebsite.com
      </li>
      <li>
        <svg viewBox="0 0 10 10"><path d="M5 0a5 5 0 1 0 0 10A5 5 0 0 0 5 0zm0 1c.7.8 1.1 2 1.2 3.5H3.8C3.9 3 4.3 1.8 5 1zM1 5.5h1.8c.1 1.2.4 2.3.9 3.2A4 4 0 0 1 1 5.5zm0-1a4 4 0 0 1 2.7-3.2c-.5.9-.8 2-.9 3.2zm4 4.5c-.7-.8-1.1-2-1.2-3.5h2.4C6.1 7 5.7 8.2 5 9zm1.3-.3c.5-.9.8-2 .9-3.2H9a4 4 0 0 1-2.7 3.2zM7.2 4.5c-.1-1.2-.4-2.3-.9-3.2A4 4 0 0 1 9 4.5z"/></svg>
        www.yourwebsite.com
      </li>
    </ul>
  </div>
</section>

</body>
</html>
```